Label design for an exciting new Vodka brand

We need a label design for a dynamic new Vodka brand called 'Pale lantern drift Vodka'. It is a crisp and versatile liquid with a clean and smooth finish. It should appeal to 21-39 year olds, with a slight female skew. Colours, fonts and styles should be modern and relatively neutral - take inspiration from the brand pictures attached.

Target Market(s)

21-39 year olds, both male and female, but with a slight female skew

```html
<!DOCTYPE html>
<html lang="en">
<head>
<meta charset="utf-8">
<title>Pale Lantern Drift Vodka — Label</title>
<link href="https://fonts.googleapis.com/css2?family=Lora:wght@400;600&display=swap" rel="stylesheet">
<style>
  :root {
    --backdrop: #e6e4df;
    --label-paper: #f1efe9;
    --grain-tone: #e7e1d2;
    --ink: #3a3a3a;
    --ink-soft: #55524c;
    --band: #1d1d1f;
    --gold: #c9a45a;
    --rule: #8a867d;
  }
  * { box-sizing: border-box; margin: 0; padding: 0; }
  html, body {
    width: 1200px; height: 698px; overflow: hidden;
    background: var(--backdrop);
  }
  .canvas {
    position: relative; width: 1200px; height: 698px;
    display: flex; align-items: center; justify-content: center;
  }
  .label {
    position: relative; width: 500px; height: 640px;
    background: var(--label-paper);
    box-shadow: 0 2px 10px rgba(0,0,0,.12);
    overflow: hidden;
  }
  .label__grain {
    position: absolute; inset: 0;
    background:
      radial-gradient(ellipse 70% 45% at 35% 20%, rgba(220,205,170,.35), transparent 70%),
      radial-gradient(ellipse 60% 40% at 70% 85%, rgba(210,200,180,.35), transparent 70%),
      linear-gradient(180deg, var(--label-paper), var(--grain-tone));
  }
  .label__band { position: absolute; left: 0; right: 0; background: var(--band); }
  .label__band--top { top: 0; height: 10px; }
  .label__band--top-thin { top: 16px; height: 3px; }
  .label__band--bottom { bottom: 0; height: 12px; }
  .label__band--bottom-thin { bottom: 18px; height: 3px; }
  .label__content {
    position: absolute; inset: 0; text-align: center; color: var(--ink);
  }
  .brand-name {
    position: absolute; top: 196px; left: 40px; right: 40px;
    font-family: "Lora", serif; font-weight: 600; font-size: 44px;
    line-height: 1.3; letter-spacing: 3px; text-transform: uppercase;
    color: var(--ink);
  }
  .tasting {
    position: absolute; top: 452px; left: 110px; right: 110px;
    font-family: "Lora", serif; font-size: 11.5px; line-height: 1.45;
    color: var(--ink-soft);
    border-top: 1px solid var(--rule); border-bottom: 1px solid var(--rule);
    padding: 8px 0 6px;
  }
  .volume {
    position: absolute; top: 552px; left: 0; right: 0;
    font-family: "Lora", serif; font-weight: 600; font-size: 12px; letter-spacing: 1px;
  }
  .gold-rules { position: absolute; left: 0; right: 0; top: 578px; }
</style>
</head>
<body>
<main class="canvas">
  <section class="label">
    <div class="label__grain" role="img" aria-label="Fine pale wood-grain pattern in cream and soft gold"></div>
    <div class="label__band label__band--top"></div>
    <div class="label__band label__band--top-thin"></div>
    <div class="label__content">
      <h1 class="brand-name">Pale Lantern<br>Drift Vodka</h1>
      <p class="tasting">It is a crisp and versatile<br>liquid with a clean and smooth finish</p>
      <p class="volume">15.9 FL.OZ. ( 500ML)</p>
      <svg class="gold-rules" width="500" height="10" viewBox="0 0 500 10">
        <line x1="70" y1="2" x2="430" y2="2" stroke="var(--gold)" stroke-width="1.4"/>
        <line x1="70" y1="7" x2="430" y2="7" stroke="var(--gold)" stroke-width="1.4"/>
      </svg>
    </div>
    <div class="label__band label__band--bottom-thin"></div>
    <div class="label__band label__band--bottom"></div>
  </section>
</main>
</body>
</html>
```